Harborlane Products Flyer

Harborlane Lending Group, Inc.
Licensed Mortgage Company
Serving the DMV since 1997
"You open the Harborlane, we'll carry the load"
We specialize in...
FHA Loans
* Credit Scores as low as 500
* 203K Renovation Loans
Conventional Loans
* As little as 1% Down
* Bank Statement for Self-Employed
Investor Loans
* DSCR, & Fix & Flip
* Commercial & New Construction
Other Programs
* HELOCS & Reverse Mortgages
Call today for a free consultation
(800) 914-6027
www.harborlanehomeloans.com
NMLS #731860

```html
<!DOCTYPE html>
<html lang="en">
<head>
<meta charset="utf-8">
<title>Harborlane Products Flyer</title>
<link rel="stylesheet" href="https://fonts.googleapis.com/css2?family=Archivo+Black&family=Montserrat:wght@500;600;700;800&family=Poppins:wght@400;500;600;700&display=swap">
<style>
  :root {
    --navy: #0b1d4a;
    --navy-deep: #071338;
    --blue: #0a5aa8;
    --blue-bright: #1673c4;
    --heading-blue: #0c6ab8;
    --gold: #f6c261;
    --gold-dark: #a8702c;
    --ink: #1c1c1c;
    --paper: #f4f4f4;
    --white: #ffffff;
  }
  * { box-sizing: border-box; margin: 0; padding: 0; }
  html, body { width: 1200px; height: 1200px; overflow: hidden; background: var(--white); }
  .canvas { position: relative; width: 1200px; height: 1200px; font-family: "Poppins", sans-serif; }
  .artwork { position: absolute; inset: 0; }

  .brand { position: absolute; left: 205px; top: 112px; width: 310px; text-align: center; color: var(--navy); }
  .brand-name { font-family: "Montserrat", sans-serif; font-weight: 800; font-size: 34px; line-height: 1.05; color: var(--navy); }
  .brand-sub { font-family: "Montserrat", sans-serif; font-weight: 800; font-size: 19px; letter-spacing: 1px; color: var(--navy); margin-top: 4px; }
  .brand-tagline { font-family: "Montserrat", sans-serif; font-weight: 700; font-size: 10.5px; color: var(--blue); margin-top: 8px; padding-bottom: 3px; border-bottom: 1.5px solid var(--blue); display: inline-block; }
  .brand-est { font-family: "Montserrat", sans-serif; font-weight: 700; font-size: 11px; letter-spacing: 3px; color: var(--gold-dark); margin-top: 4px; }

  .headline { position: absolute; left: 230px; top: 382px; }
  .headline-lead { font-family: "Montserrat", sans-serif; font-weight: 800; font-size: 45px; color: var(--ink); letter-spacing: -0.5px; line-height: 1; }
  .headline-name { font-family: "Archivo Black", sans-serif; font-size: 55px; line-height: 1; margin-top: 14px; letter-spacing: -0.5px;
    background: linear-gradient(180deg, #5a3810 0%, #a8702c 35%, #f6c261 65%, #ffd98a 100%);
    -webkit-background-clip: text; background-clip: text; color: transparent;
    -webkit-text-stroke: 1.6px var(--ink); }
  .headline-close { font-family: "Montserrat", sans-serif; color: #0d3d6e; line-height: 0.95; margin-top: 20px; }
  .headline-close .line-one { display: block; font-weight: 600; font-size: 60px; letter-spacing: -1px; }
  .headline-close .line-two { display: block; font-weight: 800; font-size: 72px; letter-spacing: -1px; }

  .specialty-pill { position: absolute; left: 437px; top: 725px; width: 332px; height: 50px; border-radius: 25px; background: var(--blue); color: var(--gold); font-family: "Montserrat", sans-serif; font-weight: 800; font-size: 30px; display: flex; align-items: center; justify-content: center; }

  .programs { position: absolute; left: 271px; top: 786px; width: 720px; display: grid; grid-template-columns: 366px 1fr; row-gap: 14px; }
  .program h3 { font-family: "Poppins", sans-serif; font-weight: 700; font-size: 29px; color: var(--heading-blue); line-height: 1.15; letter-spacing: -0.3px; }
  .program ul { list-style: none; margin-top: 4px; }
  .program li { font-family: "Poppins", sans-serif; font-weight: 500; font-size: 16.5px; color: var(--ink); line-height: 23px; padding-left: 26px; position: relative; }
  .program li::before { content: ""; position: absolute; left: 2px; top: 7px; width: 8px; height: 8px; border: 2px solid var(--heading-blue); border-radius: 50%; }

  .contact-call { position: absolute; left: 473px; top: 1008px; color: var(--white); font-family: "Poppins", sans-serif; }
  .contact-call .soft { display: block; font-size: 23px; font-weight: 500; color: #2f9be0; line-height: 1.15; }
  .contact-call .strong { display: block; font-size: 23px; font-weight: 700; line-height: 1.15; }
  .contact-divider { position: absolute; left: 717px; top: 1012px; width: 3px; height: 46px; background: var(--gold); }
  .contact-id { position: absolute; right: 222px; top: 1004px; text-align: right; }
  .contact-id .nmls { font-family: "Poppins", sans-serif; font-size: 18px; font-weight: 500; color: var(--white); }
  .contact-id .phone { font-family: "Poppins", sans-serif; font-size: 31px; font-weight: 700; color: var(--gold); line-height: 1.15; }
  .contact-web { position: absolute; left: 470px; top: 1078px; width: 555px; height: 38px; display: flex; align-items: center; justify-content: center; font-family: "Poppins", sans-serif; font-size: 23px; font-weight: 500; letter-spacing: 1.5px; color: var(--white); }
</style>
</head>
<body>
<div class="canvas">
  <svg class="artwork" viewBox="0 0 1200 1200" width="1200" height="1200">
    <defs>
      <clipPath id="sheet"><rect x="182" y="58" width="843" height="1091"/></clipPath>
      <linearGradient id="goldBand" x1="0" y1="0" x2="1" y2="0">
        <stop offset="0" stop-color="#f6c261"/><stop offset="0.5" stop-color="#ffe2a0"/><stop offset="1" stop-color="#a8702c"/>
      </linearGradient>
      <linearGradient id="goldRing" x1="0" y1="0" x2="0" y2="1">
        <stop offset="0" stop-color="#a8702c"/><stop offset="0.6" stop-color="#f6c261"/><stop offset="1" stop-color="#ffd98a"/>
      </linearGradient>
      <linearGradient id="blueSweep" x1="0" y1="0" x2="1" y2="1">
        <stop offset="0" stop-color="#1673c4"/><stop offset="1" stop-color="#0b1d4a"/>
      </linearGradient>
      <linearGradient id="navyBase" x1="0" y1="0" x2="0" y2="1">
        <stop offset="0" stop-color="#0b1d4a"/><stop offset="1" stop-color="#071338"/>
      </linearGradient>
      <linearGradient id="softPhoto" x1="0" y1="0" x2="1" y2="0">
        <stop offset="0" stop-color="#efeae6"/><stop offset="0.5" stop-color="#e3d6cf"/><stop offset="1" stop-color="#f1efed"/>
      </linearGradient>
      <linearGradient id="homePhoto" x1="0" y1="0" x2="0" y2="1">
        <stop offset="0" stop-color="#c9c2b3"/><stop offset="0.55" stop-color="#8a8f7a"/><stop offset="1" stop-color="#4f7a3a"/>
      </linearGradient>
    </defs>

    <g clip-path="url(#sheet)">
      <rect class="sheet-bg" x="182" y="58" width="843" height="1091" fill="#f4f4f4"/>
      <g role="img" aria-label="Faded photo of a smiling family relaxing together">
        <rect x="182" y="281" width="700" height="420" fill="url(#softPhoto)"/>
      </g>
      <path class="blue-sweep" d="M1025 360 L1025 706 L700 706 C790 706 828 630 848 548 C868 470 940 440 1025 420 Z" fill="url(#blueSweep)"/>
      <circle class="ring-outer" cx="806" cy="250" r="250" fill="#0a5aa8"/>
      <circle class="ring-gold" cx="806" cy="250" r="228" fill="url(#goldRing)"/>
      <g role="img" aria-label="Photo of a cheering family in front of their new house holding a home for sale sign">
        <circle cx="818" cy="252" r="210" fill="url(#homePhoto)"/>
      </g>
      <rect class="navy-base" x="182" y="706" width="843" height="443" fill="url(#navyBase)"/>
      <path class="gold-curve" d="M182 700 L700 700 C792 700 830 624 850 546" fill="none" stroke="url(#goldBand)" stroke-width="12"/>
      <polygon class="specialty-card" points="219,750 988,750 988,986 257,986 219,940" fill="#ffffff"/>
      <polygon class="corner-blue" points="182,912 325,1052 470,1052 470,1078 312,1078 182,958" fill="#0a5aa8"/>
      <polygon class="corner-gold" points="182,1020 262,1096 405,1096 440,1149 182,1149" fill="url(#goldBand)"/>
      <polygon class="corner-gold-thin" points="385,1072 410,1072 470,1149 445,1149" fill="url(#goldBand)"/>
      <path class="web-band" d="M470 1078 L1025 1078 L1025 1116 L452 1116 Q436 1097 470 1078 Z" fill="#1a5fb0"/>
    </g>
  </svg>

  <header class="brand">
    <div class="brand-name">Harborlane</div>
    <div class="brand-sub">LENDING GROUP</div>
    <div class="brand-tagline">YOU OPEN THE HARBORLANE, WE'LL CARRY THE LOAD.</div>
    <div class="brand-est">EST. 1997</div>
  </header>

  <h1 class="headline">
    <span class="headline-lead">YOU OPEN THE</span>
    <div class="headline-name">HARBORLANE</div>
    <div class="headline-close">
      <span class="line-one">WE’LL CARRY</span>
      <span class="line-two">THE LOAD</span>
    </div>
  </h1>

  <div class="specialty-pill">WE SPECIALIZE IN</div>

  <section class="programs">
    <div class="program">
      <h3>FHA Loans</h3>
      <ul><li>Credit Scores as low as 500</li><li>203K Renovation Loans</li></ul>
    </div>
    <div class="program">
      <h3>Investor Loans</h3>
      <ul><li>DSCR &amp; Fix &amp; Flip</li><li>Commercial &amp; New Construction</li></ul>
    </div>
    <div class="program">
      <h3>Conventional Loans</h3>
      <ul><li>As little as 1% Down</li><li>Bank Statement for Self-Employed</li></ul>
    </div>
    <div class="program">
      <h3>Other Programs</h3>
      <ul><li>HELOCS &amp; Reverse Mortgages</li></ul>
    </div>
  </section>

  <div class="contact-call"><span class="soft">Call today for a</span><span class="strong">Free Consultation</span></div>
  <div class="contact-divider"></div>
  <div class="contact-id"><div class="nmls">NMLS #731860</div><div class="phone">(800) 914-6027</div></div>
  <div class="contact-web">www.harborlanehomeloans.com</div>
</div>
</body>
</html>
```